Flyer Design Project

I require a double sided flyer in PSD format.
The flyer should look fresh and clean.
The flyer is for an digital marketing company that offers various services. The services are broken down into 3 main categories and the design should reflect this.
All the content is provided in the attached file
Industry/Entity Type
Digital
Requirements
Must have
- Front of the leaflet to be mainly white background with appealing text based questions in the colours in large font with relevant images.
Back if the
3 separate boxes using the colours indicated in the attachment for the services on back of the leafet.
Should not have
- Gradients
Borders on the edges of the design
Vignettes
Black elements
Any text below 10pt
Fancy fonts
Do not use old-style fonts

```html
<!DOCTYPE html>
<html lang="en">
<head>
<meta charset="utf-8">
<title>Novaro – Flyer Front</title>
<link rel="stylesheet" href="https://fonts.googleapis.com/css2?family=Anton&family=Catamaran:wght@300;400;500&family=Roboto+Condensed:ital,wght@1,700&display=swap">
<style>
  :root {
    --slate: #434b5a;
    --cyan: #4fb8d8;
    --sky: #3fb5e0;
    --white: #ffffff;
    --ink: #1c1c1c;
    --globe: #6fa9dc;
    --lime-band: rgba(180, 214, 60, 0.6);
    --lime-text: #c6e600;
    --blue-band: rgba(50, 150, 215, 0.78);
    --blue-text: #58aef0;
    --rust-band: rgba(150, 95, 60, 0.78);
    --orange-text: #ff7b00;
  }
  * { box-sizing: border-box; margin: 0; padding: 0; }
  html, body { width: 845px; height: 1200px; overflow: hidden; background: var(--white); }
  .flyer {
    position: relative;
    width: 845px; height: 1200px;
    background: var(--white);
    font-family: "Catamaran", sans-serif;
    overflow: hidden;
  }
  .brand-box {
    position: absolute; left: 36px; top: 17px; width: 318px; height: 135px;
    background: var(--slate);
    display: flex; align-items: center; justify-content: center;
  }
  .brand-name {
    font-weight: 400; font-size: 68px; letter-spacing: 1px;
    color: var(--cyan); line-height: 1;
  }
  .call-box {
    position: absolute; left: 366px; top: 15px; width: 479px; height: 137px;
    background: var(--slate); border-radius: 22px 0 0 22px;
    color: var(--white); font-size: 31px; line-height: 42px;
    display: flex; flex-direction: column; align-items: center; justify-content: center;
  }
  .call-box .phone { color: var(--cyan); }
  .globe {
    position: absolute; left: 67px; top: 218px; width: 770px; height: 770px;
  }
  .band {
    position: absolute; border-radius: 14px;
    display: flex; flex-direction: column; justify-content: center;
  }
  .band-lime { left: 60px; top: 265px; width: 580px; height: 194px; background: var(--lime-band); padding-left: 6px; }
  .band-blue { left: 36px; top: 503px; width: 555px; height: 195px; background: var(--blue-band); padding-left: 30px; }
  .band-rust { left: 63px; top: 740px; width: 564px; height: 195px; background: var(--rust-band); padding-left: 30px; }
  .question {
    font-family: "Anton", sans-serif; font-size: 44px; line-height: 48px;
    letter-spacing: -0.5px;
    -webkit-text-stroke: 1.5px var(--ink);
    text-shadow: 2px 2px 0 rgba(0,0,0,0.55);
  }
  .band-lime .question { color: var(--lime-text); }
  .band-blue .question { color: var(--blue-text); }
  .band-rust .question { color: var(--orange-text); }
  .tagline {
    position: absolute; left: 0; right: 0; top: 1008px; text-align: center;
    font-size: 36px; font-weight: 300; color: var(--ink);
  }
  .tagline strong {
    font-family: "Roboto Condensed", sans-serif; font-style: italic; font-weight: 700;
  }
  .web-box {
    position: absolute; left: 36px; top: 1094px; width: 318px; height: 88px;
    background: var(--slate); color: var(--white);
    font-size: 27px; display: flex; align-items: center; justify-content: center;
  }
  .web-box .accent { color: var(--cyan); }
  .address-box {
    position: absolute; left: 360px; top: 1094px; width: 485px; height: 88px;
    background: var(--sky); border-radius: 20px 0 0 20px; color: var(--white);
    font-size: 21px; line-height: 28px;
    display: flex; flex-direction: column; align-items: center; justify-content: center;
  }
</style>
</head>
<body>
<main class="flyer">
  <header>
    <div class="brand-box"><span class="brand-name">NOVARO</span></div>
    <div class="call-box">
      <span>Call <span class="phone">0121 496 0718</span> for</span>
      <span>a FREE consultation</span>
    </div>
  </header>

  <svg class="globe" viewBox="0 0 770 770" role="img" aria-label="Illustration of a blue world globe with a magnifying glass over Europe">
    <circle cx="385" cy="385" r="385" fill="var(--globe)"/>
  </svg>

  <section class="band band-lime">
    <p class="question">Did You Know 85% of<br>Consumers Use The Internet<br>To Find Businesses Like Yours?</p>
  </section>
  <section class="band band-blue">
    <p class="question">Are Your Customers<br>Finding You Online?</p>
  </section>
  <section class="band band-rust">
    <p class="question">Do You Need More Customers<br>For Your Business?</p>
  </section>

  <p class="tagline">Let us help you <strong>grow your business online</strong></p>

  <footer>
    <div class="web-box">www.<span class="accent">novaro</span>.co.uk</div>
    <div class="address-box">
      <span>24 Linden Yard | 85 Harbour Road</span>
      <span>Brookfield | BK4 2LT | 0121 496 0718</span>
    </div>
  </footer>
</main>
</body>
</html>
```